Album Cover Art for New Single

Independent singer-songwriter and pianist, seeking design work for a new single "Walk Beside the Lantern". Christian & Gospel music format. See attached for master recording.

This single is personal for me, so I'm looking for an image that really captures the heart of the message. Redemption, forgiveness, prodigals returning home to a loving father.
Updates

Target Market(s)

Millenials

Colors

Designer to choose colors to be used in the design.

Requirements
Must have
• simple graphic, must include the following text:
• Walk Beside the Lantern
• Dale Verrick
Should not have
• Avoid "cheesy" look and feel.

```html
<!DOCTYPE html>
<html lang="en">
<head>
<meta charset="utf-8">
<title>Walk Beside the Lantern — Dale Verrick</title>
<link rel="stylesheet" href="https://fonts.googleapis.com/css2?family=Oswald:wght@200;300&family=Cormorant+Garamond:wght@500&display=swap">
<style>
  :root {
    --fog-top: #dcdcda;
    --fog-mid: #c9c6c0;
    --grass-light: #9a7d5a;
    --grass-dark: #5e4630;
    --path-earth: #4a3624;
    --title-white: #ffffff;
  }
  html, body {
    margin: 0;
    padding: 0;
    width: 1200px;
    height: 1200px;
    overflow: hidden;
    background: var(--fog-top);
  }
  .cover {
    position: relative;
    width: 1200px;
    height: 1200px;
    overflow: hidden;
  }
  .cover-photo {
    position: absolute;
    inset: 0;
    background:
      radial-gradient(ellipse 30% 40% at 33% 100%, var(--path-earth) 0%, transparent 70%),
      linear-gradient(to bottom,
        var(--fog-top) 0%,
        var(--fog-mid) 38%,
        var(--grass-light) 55%,
        var(--grass-dark) 100%);
  }
  .cover-title {
    position: absolute;
    inset: 0;
    width: 1200px;
    height: 1200px;
  }
  .cover-title text {
    font-family: "Oswald", "Arial Narrow", sans-serif;
    font-weight: 200;
    font-size: 250px;
    fill: var(--title-white);
    text-transform: uppercase;
  }
  .artist-name {
    position: absolute;
    left: 0;
    right: 0;
    bottom: 52px;
    margin: 0;
    text-align: center;
    font-family: "Cormorant Garamond", Georgia, serif;
    font-weight: 500;
    font-size: 25px;
    letter-spacing: 0.38em;
    color: var(--title-white);
    text-transform: uppercase;
  }
</style>
</head>
<body>
  <main class="cover">
    <div class="cover-photo" role="img" aria-label="Photograph: a young man in a quilted jacket walking away along a narrow dirt path through brown winter grass toward a misty line of bare trees"></div>

    <svg class="cover-title" viewBox="0 0 1200 1200" aria-label="Walk Beside the Lantern">
      <text transform="translate(18 790) rotate(-13)" textLength="1175" lengthAdjust="spacingAndGlyphs">Walk Beside</text>
      <text transform="translate(92 1068) rotate(-13)" textLength="1110" lengthAdjust="spacingAndGlyphs">The Lantern</text>
    </svg>

    <p class="artist-name">Dale Verrick</p>
  </main>
</body>
</html>
```